Ridge Lass Crew (Flyer)

I want a flyer to advertise my service.
Details below, and logo's to use are attached.

A girls only after school program, 11-14yrs, as OSHC is no longer avail, dedicated to coaching & mentoring our girls into strong, independent young women.

The Brainchild of Rebecca Folwin, Ridge Lass Crew was created to address the growing demand for after school/school holiday supervision for kids moving from primary into high school, when OSHC ceases to exist.
With over 12 years experience mentoring and coaching young women in the corporate world, Bec decided to leave her role as a Director with Tarrant Trust, and follow her passion.
Bec, along with her sister Lorraine, who has over 10 years experience in local communities as a Youth Worker, and is also a qualified Enrolled Nurse, embarked on building a program designed to keep parents happy (by knowing their girls are safe) and dedicated to coaching and mentoring our girls into strong, independent young women.
Open every afternoon and during school holidays, we look to offer;
- Daily meditation
- Healthy snacks
- Dedicated homework time
- Organised group activity, led by qualified instructors (yoga, fitness class, soccer etc)
- Regular guests speakers, addressing issues/concerns for young people today
- SOCIAL MEDIA FREE ZONE

Located 87 Pelham Pde, Baulkham Hills (across from Crestmoor Day Clinic)
Open 3-6pm Monday to Friday

Facebook page: http://fb.example/ridgelasscrew
Email: info@ridgelasscrew.example.au
Mobile: 0455817396

Target Market(s)

Parents of teenage girls, teenage girls 11-14 years

Industry/Entity Type

School

Font styles to use
Sans Serif

Colors
b768aa
e667a6

Requirements
Must have
• What progam is - see brief
• Who runs it
Should not have
• Not be too busy, not overly mature images

```html
<!DOCTYPE html>
<html lang="en">
<head>
<meta charset="utf-8">
<title>Ridge Lass Crew – After School Program Flyer</title>
<link rel="stylesheet" href="https://fonts.googleapis.com/css2?family=Cinzel:wght@600;700&family=Noto+Sans:wght@400&family=Open+Sans:wght@600;700&family=Roboto+Condensed:wght@400;700&family=Source+Sans+3:wght@400&display=swap">
<style>
  :root {
    --purple: #b65ce0;
    --purple-deep: #a94bd6;
    --headline-box: #b25fe6;
    --magenta: #e64fd8;
    --pink-light: #fbc6f6;
    --hot-pink: #e4307f;
    --pin-pink: #ef3f8c;
    --ink: #2a0c38;
    --phone-ink: #3d1a45;
    --white: #ffffff;
  }
  html, body { margin: 0; padding: 0; overflow: hidden; }
  body { width: 934px; height: 1200px; background: var(--purple); }
  .flyer { position: relative; width: 934px; height: 1200px; overflow: hidden; background: var(--purple); }
  .hero-photo {
    position: absolute; left: 16px; top: 24px; width: 918px; height: 1080px;
    background: linear-gradient(100deg, #e4e0e3 0%, #d9d6da 40%, #cfcbcf 62%, #d8b9a6 78%, #b98a72 100%);
  }
  .shapes { position: absolute; inset: 0; }
  .logo-box {
    position: absolute; left: 16px; top: 70px; width: 268px; height: 322px;
    background: var(--white); display: flex; align-items: center; justify-content: center;
  }
  .logo-name {
    font-family: "Open Sans", sans-serif; font-weight: 700; font-size: 40px; line-height: 1.1;
    color: var(--magenta); text-align: center; margin: 0;
  }
  .headline {
    position: absolute; left: 436px; top: 162px; width: 402px; height: 228px;
    background: var(--headline-box); border-radius: 12px; color: var(--ink); text-align: center;
  }
  .headline-line { margin: 0; font-family: "Cinzel", serif; font-weight: 700; white-space: nowrap; }
  .headline-main { font-size: 42px; line-height: 1; padding-top: 18px; }
  .headline-sub { font-size: 29px; line-height: 1; margin-top: 14px; margin-left: 4px; }
  .headline-age { font-size: 42px; line-height: 1; margin-top: 14px; }
  .headline-note { font-family: "Open Sans", sans-serif; font-weight: 600; font-size: 22px; margin: 8px 0 0; letter-spacing: -0.3px; }
  .section-title {
    position: absolute; margin: 0; font-family: "Open Sans", sans-serif; font-weight: 700;
    font-size: 30px; color: var(--hot-pink); letter-spacing: -0.5px;
  }
  .offer-title { left: 66px; top: 466px; }
  .about-title { left: 68px; top: 798px; }
  .offer-list {
    position: absolute; left: 64px; top: 520px; margin: 0; padding: 0; list-style: none;
    font-family: "Noto Sans", sans-serif; font-size: 19px; color: var(--ink); letter-spacing: 0.3px;
  }
  .offer-list li { position: absolute; left: 0; white-space: nowrap; padding-left: 18px; line-height: 22px; }
  .offer-list li::before {
    content: ""; position: absolute; left: 2px; top: 5px;
    border-left: 7px solid var(--hot-pink); border-top: 6px solid transparent; border-bottom: 6px solid transparent;
  }
  .about-text {
    position: absolute; left: 62px; top: 842px; width: 410px; margin: 0;
    font-family: "Source Sans 3", sans-serif; font-size: 18.5px; line-height: 29.6px; color: var(--ink);
  }
  .call-text {
    position: absolute; left: 747px; top: 782px; width: 110px; margin: 0; text-align: center;
    font-family: "Noto Sans", sans-serif; font-size: 22px; line-height: 36px; color: var(--ink);
  }
  .phone {
    position: absolute; right: 28px; top: 918px; margin: 0;
    font-family: "Roboto Condensed", sans-serif; font-size: 44px; color: var(--phone-ink); letter-spacing: 0.5px;
  }
  .founder {
    position: absolute; right: 6px; top: 986px; margin: 0; font-family: "Cinzel", serif; font-weight: 700;
    font-size: 24px; color: var(--ink); white-space: nowrap;
  }
  .brand-sign {
    position: absolute; right: 4px; top: 1026px; margin: 0; font-family: "Cinzel", serif; font-weight: 600;
    font-size: 38px; color: var(--ink); letter-spacing: 1px; white-space: nowrap;
  }
  .footer-contact {
    position: absolute; top: 1134px; margin: 0; display: flex; align-items: center; gap: 8px;
    font-family: "Roboto Condensed", sans-serif; font-weight: 700; font-size: 17px; color: var(--white); white-space: nowrap;
  }
  .contact-web { left: 32px; }
  .contact-mail { left: 286px; }
  .contact-address { left: 530px; top: 1128px; align-items: flex-start; line-height: 18px; }
  .contact-address small { font-size: 14px; display: block; }
  .icon { flex: none; }
</style>
</head>
<body>
<main class="flyer">
  <div class="hero-photo" role="img" aria-label="Photo of a girl wearing a white t-shirt printed with the program name"></div>

  <svg class="shapes" width="934" height="1200" viewBox="0 0 934 1200" aria-hidden="true">
    <polygon points="860,48 934,48 934,130" fill="var(--magenta)"/>
    <polygon points="0,392 300,392 520,660 934,800 934,1104 0,1104" fill="var(--magenta)"/>
    <polygon points="0,440 312,440 512,690 934,826 934,1104 0,1104" fill="var(--pink-light)"/>
    <polygon points="0,940 60,1030 420,1092 934,1100 934,1104 0,1104" fill="var(--magenta)"/>
    <polygon points="56,1034 416,1060 424,1092" fill="#1c1420"/>
    <polygon points="0,1104 934,1104 934,1200 0,1200" fill="var(--purple)"/>
    <polygon points="0,1100 360,1104 0,1110" fill="var(--purple-deep)"/>
    <g class="call-pin">
      <path d="M802 744 a74 74 0 0 1 52 126 L802 912 L750 870 a74 74 0 0 1 52 -126 Z" fill="var(--pin-pink)" stroke="#2a0c38" stroke-width="4"/>
      <circle cx="802" cy="814" r="56" fill="var(--white)" stroke="var(--pin-pink)" stroke-width="3"/>
    </g>
  </svg>

  <div class="logo-box">
    <p class="logo-name">Ridge<br>Lass<br>Crew</p>
  </div>

  <section class="headline">
    <p class="headline-line headline-main">A Girls Only</p>
    <p class="headline-line headline-sub">After School Program</p>
    <p class="headline-line headline-age">For 11-14yrs</p>
    <p class="headline-note">as OSHC is no longer available</p>
  </section>

  <h2 class="section-title offer-title">WE OFFER</h2>
  <ul class="offer-list">
    <li style="top:0">Daily meditation</li>
    <li style="top:46px">Healthy snacks</li>
    <li style="top:94px">Organised group activity,<br>(yoga, fitness class, soccer etc.)</li>
    <li style="top:152px">Regular guests speakers</li>
    <li style="top:195px">Dedicated homework time</li>
    <li style="top:238px">Social media free zone</li>
  </ul>

  <h2 class="section-title about-title">ABOUT US</h2>
  <p class="about-text">The Brainchild of Rebecca Folwin, Ridge Lass Crew was created to address the growing demand for after school/school holiday super&shy;vision for kids moving from primary into high school, when OSHC ceases to exist.</p>

  <p class="call-text">CALL<br>NOW</p>
  <p class="phone">0455817396</p>
  <p class="founder">The Brainchild of Rebecca Folwin</p>
  <p class="brand-sign">Ridge Lass Crew</p>

  <p class="footer-contact contact-web">
    <svg class="icon" width="12" height="12" viewBox="0 0 12 12" aria-hidden="true"><circle cx="6" cy="6" r="5" fill="var(--white)"/></svg>
    http://fb.example/ridgelasscrew
  </p>
  <p class="footer-contact contact-mail">
    <svg class="icon" width="18" height="13" viewBox="0 0 18 13" aria-hidden="true"><rect x="0.5" y="0.5" width="17" height="12" rx="1.5" fill="var(--white)"/><path d="M1 1.5 L9 7.5 L17 1.5" fill="none" stroke="var(--purple)" stroke-width="1.6"/></svg>
    info@ridgelasscrew.example.au
  </p>
  <p class="footer-contact contact-address">
    <svg class="icon" width="24" height="32" viewBox="0 0 24 32" aria-hidden="true"><path d="M12 1 a11 11 0 0 1 11 11 c0 8 -11 19 -11 19 S1 20 1 12 A11 11 0 0 1 12 1 Z" fill="var(--white)"/><circle cx="12" cy="12" r="4.5" fill="var(--purple)"/></svg>
    <span>87 Pelham Pde, Baulkham Hills<small>(across from Crestmoor Day Clinic)</small></span>
  </p>
</main>
</body>
</html>
```